Tellmora Corporate Stationery

Look for design of all new corporate stationery for an existing insurance broking business that is going through a redesign and move from older partners to younger family members. New Logo is attached. Company is Brisbane based.
Colours in the Logo is Hex #43bed8 and website features a lot of hex #17b8d8. Website front page "A plan to protect you" - headline. "Professional and Individual advice to protect your greatest assets" - tagline.

Stationery required: Business Cards, Letter head, Thank-you cards, Birthday cards, Presentation folders, With Compliment slips and a powerpoint template. We also would like to send a card to all customers with the something along of the lines of "something new".

Target Market(s)

Customers of Insurance business looking at superannuation, life and income protection insurance, investment advice and wills

Industry/Entity Type

Insurance Broker

Font styles to use
Other font styles liked:
• same as logo

Requirements
Must have
• The above designs for new stationery for the new business including:
• Business Cards, Letter head, Thank-you cards, Birthday cards, Presentation folders, With Compliment slips and a powerpoint template. We also would like to send a card to all customers with the something along of the lines of "something new".
Nice to have
• It is a new look - long time family business being passed to next generation - big focus on advice for YOU, individual advice etc..

```html
<!DOCTYPE html>
<html lang="en">
<head>
<meta charset="utf-8">
<title>Tellmora – Thank You Card</title>
<link href="https://fonts.googleapis.com/css2?family=Maven+Pro:wght@400;500&display=swap" rel="stylesheet">
<style>
  :root {
    --page-bg: #ffffff;
    --card-bg: #ffffff;
    --ink: #7f7f83;
    --ink-soft: #8a8a8e;
    --rule: #7f7f83;
  }
  * { margin: 0; padding: 0; box-sizing: border-box; }
  html, body {
    width: 1200px;
    height: 1000px;
    overflow: hidden;
    background: var(--page-bg);
    font-family: "Maven Pro", "Trebuchet MS", sans-serif;
  }
  body { position: relative; }
  .thank-you-card {
    position: absolute;
    left: 212px;
    top: 0;
    width: 774px;
    height: 1000px;
    background: var(--card-bg);
    box-shadow: 0 0 8px rgba(0, 0, 0, 0.18), 3px 0 6px rgba(0, 0, 0, 0.08);
  }
  .greeting {
    position: absolute;
    left: 0;
    right: 0;
    top: 92px;
    text-align: center;
    color: var(--ink);
    font-weight: 500;
  }
  .greeting__main {
    display: block;
    font-size: 69px;
    line-height: 76px;
    letter-spacing: 1px;
    word-spacing: 8px;
  }
  .greeting__joiner {
    display: flex;
    justify-content: center;
    align-items: center;
    gap: 50px;
    height: 56px;
    font-size: 40px;
    font-weight: 400;
    letter-spacing: 1px;
  }
  .greeting__rule {
    width: 100px;
    height: 5px;
    background: var(--rule);
    margin-top: 6px;
  }
  .greeting__closing {
    display: block;
    font-size: 54px;
    line-height: 60px;
    font-weight: 400;
    letter-spacing: 1px;
    word-spacing: 6px;
  }
  .message {
    position: absolute;
    left: 206px;
    width: 364px;
    top: 409px;
    color: var(--ink-soft);
    font-size: 23px;
    line-height: 41px;
    letter-spacing: 0.6px;
    text-align: justify;
    text-align-last: center;
  }
</style>
</head>
<body>
  <section class="thank-you-card" aria-label="Tellmora thank you card">
    <h1 class="greeting">
      <span class="greeting__main">Thank you</span>
      <span class="greeting__joiner">
        <span class="greeting__rule" aria-hidden="true"></span>
        <span>for</span>
        <span class="greeting__rule" aria-hidden="true"></span>
      </span>
      <span class="greeting__closing">your business</span>
    </h1>
    <p class="message">You’ve put your future in the right hands, our professionals are determined to help you out when you need it the most.</p>
  </section>
</body>
</html>
```